business card deign

Logo needs the following on it.
1. attached logo
2. Tagline - "If it chills the cooler or lifts the crowd...we bring it!"
3. Name- Dalton Pikes, Founder and CPO
4. Address - 412 E. Carver Avenue, Ste 2207, Tampa, FL. 33917
5. Phone - 555.318.4726

```html
<!DOCTYPE html>
<html lang="en">
<head>
<meta charset="utf-8">
<title>Boundley Business Card</title>
<link href="https://fonts.googleapis.com/css2?family=Montserrat:wght@300;400;700&display=swap" rel="stylesheet">
<style>
  :root {
    --backdrop: #e9e6e1;
    --card: #ffffff;
    --ink: #111111;
    --ink-soft: #333333;
    --on-ink: #ffffff;
  }
  * { box-sizing: border-box; margin: 0; padding: 0; }
  html, body { width: 1200px; height: 821px; overflow: hidden; }
  body {
    background: var(--backdrop);
    font-family: "Montserrat", sans-serif;
    color: var(--ink);
    position: relative;
  }
  .card {
    position: absolute;
    width: 560px;
    height: 320px;
    background: var(--card);
    border-radius: 24px;
    overflow: hidden;
    box-shadow: 0 6px 18px rgba(0,0,0,0.18);
  }
  .card-front { left: 60px; top: 80px; }
  .card-back  { left: 580px; top: 420px; }

  .brand {
    position: absolute;
    left: 0; right: 0; top: 150px;
    display: flex; align-items: center; justify-content: center; gap: 18px;
  }
  .brand-mark {
    width: 30px; height: 30px; border-radius: 50%;
    background: var(--ink);
  }
  .brand-name {
    font-weight: 700;
    font-size: 40px;
    letter-spacing: 14px;
    color: var(--ink);
  }
  .tagline-band {
    position: absolute;
    left: 0; right: 64px; bottom: 44px;
    height: 22px;
    background: var(--ink);
    display: flex; align-items: center; justify-content: flex-end;
    padding-right: 12px;
  }
  .tagline {
    color: var(--on-ink);
    font-size: 12px;
    font-weight: 400;
    white-space: nowrap;
  }
  .band-end {
    position: absolute;
    right: 0; bottom: 44px;
    width: 24px; height: 22px;
    background: var(--ink);
  }
  .band-dot {
    position: absolute;
    right: 34px; bottom: 47px;
    width: 16px; height: 16px; border-radius: 50%;
    background: var(--ink);
  }

  .contact-row {
    position: absolute;
    left: 60px; top: 110px;
    display: flex; align-items: center; gap: 24px;
  }
  .person { text-align: right; }
  .person-name { font-weight: 700; font-size: 25px; line-height: 1.1; white-space: nowrap; }
  .person-title { font-weight: 300; font-size: 18px; color: var(--ink-soft); white-space: nowrap; }
  .divider { width: 1.5px; height: 96px; background: var(--ink); }
  .details { font-size: 15px; font-weight: 400; line-height: 1.35; color: var(--ink-soft); white-space: nowrap; }
  .phone { display: flex; align-items: center; gap: 6px; margin-bottom: 14px; }
  .phone svg { width: 14px; height: 14px; }
</style>
</head>
<body>
  <section class="card card-front">
    <div class="brand">
      <span class="brand-mark"></span>
      <span class="brand-name">BOUNDLEY</span>
    </div>
    <div class="tagline-band">
      <span class="tagline">If it chills the cooler or lifts the crowd...we bring it!</span>
    </div>
    <span class="band-dot"></span>
    <span class="band-end"></span>
  </section>

  <section class="card card-back">
    <div class="contact-row">
      <div class="person">
        <div class="person-name">Dalton Pikes</div>
        <div class="person-title">Founder and CPO</div>
      </div>
      <div class="divider"></div>
      <div class="details">
        <div class="phone">
          <svg viewBox="0 0 24 24" aria-hidden="true"><path fill="currentColor" d="M6.6 10.8a15.1 15.1 0 0 0 6.6 6.6l2.2-2.2c.3-.3.7-.4 1-.2 1.1.4 2.3.6 3.6.6.6 0 1 .4 1 1V20c0 .6-.4 1-1 1A17 17 0 0 1 3 4c0-.6.4-1 1-1h3.5c.6 0 1 .4 1 1 0 1.3.2 2.5.6 3.6.1.3 0 .7-.2 1z"/></svg>
          <span>555.318.4726</span>
        </div>
        <div>412 E. Carver Avenue, Ste</div>
        <div>2207, Tampa, FL. 33917</div>
      </div>
    </div>
  </section>
</body>
</html>
```